Basic / Quick Business Card

Quick easy design project!

Need a one sided basic business card that matches font & style of brand and bottle label for our gourmet condiment, Brindle Harrow Sauce. Brindle Harrow Sauce is sold in specialty retail, gourmet groceries and appears on chef-driven restaurant menus, so the target market is a high end, gourmet, artisan-made food-loving customer.

Files Included:
Sauce Bottle Label
Brindle Harrow Sauce Round Logos

**About the logos - the logo may be used in a circle or alone vertically as on side of the bottle label**

Layout of Card:
May be vertical or horizontal based on designer ideas.

Logo usage (in circle vs. stand alone vertical logo) is up to designers descretion as well.

Reverse side of business card will be various high end / professional product photos / food shots using us.kelbo.com system. **Designer on this project will NOT design a reserve for the card.**

Paper that will be used for printing:
Kelbo Standard - it's a WHITE paper, but we use a cream background on Brindle Harrow Sauce branding, so please take this into account on design to stay brand consistent.

Elements & Copy for Card:
1. Logo in either script horizontal or vertical version
2. Copy: "Artisan Made - Small Batch"
3. Name - Wes Dorrance
4. Title - Creator
5. Phone - xxx.xxx.xxxx
6. xxxx@brindleharrow.com
7. URL: brindleharrowsauce.com
8. Social Media: @getbrindleharrow on Quillo / Pagora / Lumigrid

Please provide final files in Illustrator or InDesign format.

```html
<!DOCTYPE html>
<html lang="en">
<head>
<meta charset="utf-8">
<title>Brindle Harrow Sauce – Business Card</title>
<link rel="stylesheet" href="https://fonts.googleapis.com/css2?family=Source+Sans+3:wght@400;600;700&family=Sorts+Mill+Goudy&display=swap">
<style>
  :root {
    --backdrop: #e9e6e1;
    --card-gold: #f2b417;
    --ink: #231f20;
    --ink-soft: #3a3433;
    --icon-grey: #5b5552;
  }
  * { box-sizing: border-box; margin: 0; padding: 0; }
  html, body {
    width: 1200px; height: 804px; overflow: hidden;
    background: var(--backdrop);
  }
  .card {
    position: absolute; left: 60px; top: 94px;
    width: 1080px; height: 617px;
    background: var(--card-gold);
    box-shadow: 0 10px 28px rgba(0,0,0,.18);
    color: var(--ink);
    font-family: "Source Sans 3", Arial, sans-serif;
    overflow: hidden;
  }
  .card__swoosh { position: absolute; inset: 0; width: 100%; height: 100%; }
  .brand-name {
    position: absolute; left: 86px; top: 150px;
    font-family: "Source Sans 3", Arial, sans-serif;
    font-weight: 700; color: var(--ink);
    line-height: .98;
  }
  .brand-name__line { display: block; font-size: 70px; letter-spacing: -1px; }
  .brand-name__line--small { font-size: 30px; letter-spacing: 8px; margin-top: 8px; padding-left: 150px; }
  .tagline {
    position: absolute; left: 86px; bottom: 48px;
    font-family: "Sorts Mill Goudy", Georgia, serif;
    color: var(--ink); line-height: 1.15;
  }
  .tagline__lead { font-size: 27px; }
  .tagline__line { font-size: 22px; }
  .contact {
    position: absolute; right: 58px; top: 58px;
    text-align: right;
  }
  .contact__name { font-size: 38px; font-weight: 700; letter-spacing: -.3px; line-height: 1.1; }
  .contact__title { font-size: 27px; font-weight: 400; line-height: 1.1; }
  .contact__list { list-style: none; margin-top: 66px; }
  .contact__item {
    display: flex; justify-content: flex-end; align-items: center; gap: 8px;
    font-size: 25px; line-height: 1; margin-bottom: 19px; color: var(--ink);
  }
  .contact__icon { width: 20px; height: 20px; flex: none; }
  .social { margin-top: 26px; }
  .social__heading {
    font-family: "Sorts Mill Goudy", Georgia, serif;
    font-size: 26px; color: var(--ink);
  }
  .social__list {
    list-style: none; display: flex; justify-content: flex-end; gap: 14px;
    margin-top: 8px;
  }
  .social__item {
    display: flex; align-items: center; gap: 5px;
    font-size: 16px; font-weight: 600; color: var(--ink-soft);
  }
  .social__dot {
    width: 13px; height: 13px; border-radius: 50%;
    background: var(--icon-grey);
  }
</style>
</head>
<body>
<article class="card">
  <svg class="card__swoosh" viewBox="0 0 1080 617" aria-hidden="true">
    <path d="M452 98 C 408 300, 488 520, 672 617 L 630 617 C 470 530, 410 330, 452 98 Z" fill="var(--ink)"/>
  </svg>

  <h1 class="brand-name">
    <span class="brand-name__line">Brindle</span>
    <span class="brand-name__line">Harrow</span>
    <span class="brand-name__line brand-name__line--small">sauce</span>
  </h1>

  <p class="tagline">
    <span class="tagline__lead">sweet &amp; spicy</span><br>
    <span class="tagline__line">made in mississippi</span><br>
    <span class="tagline__line">Artisan Made - Small Batch</span>
  </p>

  <section class="contact">
    <h2 class="contact__name">Wes Dorrance</h2>
    <p class="contact__title">Creator</p>
    <ul class="contact__list">
      <li class="contact__item">
        <svg class="contact__icon" viewBox="0 0 20 20" aria-hidden="true">
          <circle cx="10" cy="10" r="9" fill="none" stroke="var(--ink)" stroke-width="1.6"/>
          <path d="M7 5 L9 5 L9.6 8 L8.4 9 C9 10.6 9.6 11.3 11 12 L12 10.8 L15 11.4 L15 13.4 C 10 14 6 10 7 5 Z" fill="var(--ink)"/>
        </svg>
        123-456-7890
      </li>
      <li class="contact__item">
        <svg class="contact__icon" viewBox="0 0 20 20" aria-hidden="true">
          <rect x="1.5" y="4.5" width="17" height="11" rx="1.5" fill="var(--ink)"/>
          <path d="M2.5 5.5 L10 11 L17.5 5.5" fill="none" stroke="var(--card-gold)" stroke-width="1.4"/>
        </svg>
        wdorrance@brindleharrow.com
      </li>
      <li class="contact__item">
        <svg class="contact__icon" viewBox="0 0 20 20" aria-hidden="true">
          <circle cx="10" cy="10" r="8.2" fill="none" stroke="var(--ink)" stroke-width="1.6"/>
          <ellipse cx="10" cy="10" rx="3.6" ry="8.2" fill="none" stroke="var(--ink)" stroke-width="1.3"/>
          <path d="M2 10 H18 M3.5 6 H16.5 M3.5 14 H16.5" stroke="var(--ink)" stroke-width="1.2"/>
        </svg>
        www.brindleharrowsauce.com
      </li>
    </ul>
    <div class="social">
      <p class="social__heading">Follow Us On</p>
      <ul class="social__list">
        <li class="social__item"><span class="social__dot"></span>Pagora</li>
        <li class="social__item"><span class="social__dot"></span>Quillo</li>
        <li class="social__item"><span class="social__dot"></span>Lumigrid</li>
      </ul>
    </div>
  </section>
</article>
</body>
</html>
```